Redo a PPT pres. - Real Estate in Brazil - Socially equitable investments in Social Housing

We need to redo the presentation attached. It is an institutional presentation to attract local and foreign investors to invest in Brazilian Social Housing Projects structured by our company "TLR".
A middle class of 100 million, a housing deficit of 9M, a strong political will & positive income generation trends constitute grounds for a significant demand in social housing.
This make a perfect scheme for investors to invest in Brazilian Social Housing.
"TLR", is a consulting "boutique" focused in Brazilian real estate, specialized in structuring, analyzing and originating Brazilian social housing projects.
TLR is part of the group TLB. TLB is structured to create value through each step of the residential real estate business - structuring, financing, sales, marketing and technology.
We would like to see designs that use mainly the color blue. The final design should communicate financial safety and professionalism. In order to reach our needs, the designer will need to have basic understanding of finance and investment in order to highlight the most important information.
The idea is to receive back the PPT with each page redesigned and an homogeneous identity.
To all designers,
Target Market(s)
Institutional Investors and wealthy individuals
Industry/Entity Type
Residential
Look and feel

```html
<!DOCTYPE html>
<html lang="en">
<head>
<meta charset="utf-8">
<title>TLR – Investor Presentation</title>
<link rel="stylesheet" href="https://fonts.googleapis.com/css2?family=Arimo:wght@400;700&display=swap">
<style>
  :root{
    --stage:#0b0c0e;
    --navy:#1e2c5a;
    --navy-deep:#16203f;
    --sky:#5b73a8;
    --city:#2d3f73;
    --ribbon:#1b1f2b;
    --band:#262a33;
    --green:#8cc63f;
    --ink:#222222;
    --muted:#9aa3b5;
    --white:#ffffff;
  }
  *{box-sizing:border-box;margin:0;padding:0}
  html,body{width:1200px;height:520px;overflow:hidden;background:var(--stage);font-family:"Arimo",Arial,sans-serif}
  .stage{position:relative;width:1200px;height:520px}

  .slide{position:absolute;top:60px;width:532px;height:399px;overflow:hidden;background:var(--white)}
  .slide--agenda{left:44px}
  .slide--section{left:623px}

  /* photo areas */
  .city-photo{position:absolute;top:0;bottom:0;
    background:linear-gradient(180deg,var(--sky) 0%,#4a64a0 30%,var(--city) 55%,var(--navy-deep) 100%)}
  .slide--agenda .city-photo{left:0;width:194px}
  .slide--section .city-photo{left:0;right:0;
    background:linear-gradient(180deg,#7f97c6 0%,#5b76b0 28%,#3d5592 48%,var(--city) 70%,var(--navy-deep) 100%)}
  .focus-column{position:absolute;left:169px;width:194px;top:0;bottom:0;background:rgba(22,32,63,.45)}

  /* brand ribbon */
  .brand-ribbon{position:absolute;top:0;width:102px;height:96px}
  .slide--agenda .brand-ribbon{left:38px}
  .slide--section .brand-ribbon{left:223px}
  .brand-ribbon svg{position:absolute;inset:0}
  .brand-name{position:absolute;left:0;right:0;top:26px;text-align:center;color:var(--white);
    font-size:19px;font-weight:400;letter-spacing:.5px}

  .headline{position:absolute;left:18px;top:188px;color:var(--white);font-weight:700;font-size:15.5px;letter-spacing:.2px}

  .footer-band{position:absolute;left:0;top:350px;width:208px;height:30px}

  /* agenda list */
  .agenda{position:absolute;left:268px;top:60px;list-style:none}
  .agenda-item{display:flex;align-items:center;height:38.5px}
  .agenda-num{flex:0 0 34px;height:34px;border-radius:50%;background:var(--green);color:var(--white);
    font-size:11px;display:flex;align-items:center;justify-content:center;margin-right:12px}
  .agenda-text{font-size:8.5px;line-height:1.45;color:var(--ink)}
  .agenda-text strong{font-weight:700;display:block}

  .pager{position:absolute;top:372px;display:flex;align-items:center;gap:5px;font-size:9.5px}
  .slide--agenda .pager{left:469px;color:var(--navy)}
  .slide--section .pager{left:469px;color:var(--green)}
  .pager svg{width:6px;height:10px}

  /* section badge */
  .badge{position:absolute;left:203px;top:158px;width:126px;height:126px;border-radius:50%;
    background:rgba(255,255,255,.35);display:flex;align-items:center;justify-content:center}
  .badge-inner{width:108px;height:108px;border-radius:50%;background:var(--white);
    display:flex;align-items:center;justify-content:center;color:var(--navy);font-size:14px}
  .section-title{position:absolute;left:169px;width:194px;top:318px;text-align:center;color:var(--white);
    font-weight:700;font-size:12.5px;line-height:1.3}
</style>
</head>
<body>
<main class="stage">

  <section class="slide slide--agenda">
    <div class="city-photo" role="img" aria-label="Blue-toned aerial view of a city skyline by the harbour"></div>
    <div class="brand-ribbon">
      <svg viewBox="0 0 102 96" aria-hidden="true"><polygon points="0,0 102,0 102,96 51,80 0,96" fill="var(--ribbon)"/></svg>
      <div class="brand-name">TLR</div>
    </div>
    <h1 class="headline">THE TIME IS NOW!</h1>
    <svg class="footer-band" viewBox="0 0 208 30" aria-hidden="true"><polygon points="0,0 208,0 196,15 208,30 0,30" fill="var(--band)"/></svg>

    <ol class="agenda">
      <li class="agenda-item"><span class="agenda-num">1.</span><p class="agenda-text"><strong>Macro-environment &amp; Mortgage market:</strong>Green Light</p></li>
      <li class="agenda-item"><span class="agenda-num">2.</span><p class="agenda-text"><strong>A sophisticated &amp; successful program:</strong>Catalyst</p></li>
      <li class="agenda-item"><span class="agenda-num">3.</span><p class="agenda-text"><strong>Investment Structure of a typical project:</strong>Leverage &amp; Limited Risks</p></li>
      <li class="agenda-item"><span class="agenda-num">4.</span><p class="agenda-text"><strong>Small &amp; mid size developers:</strong>A partner by choice</p></li>
      <li class="agenda-item"><span class="agenda-num">5.</span><p class="agenda-text"><strong>TLM:</strong>Value added &amp; Risk mitigation</p></li>
      <li class="agenda-item"><span class="agenda-num">6.</span><p class="agenda-text"><strong>TLB:</strong>TLR, part of an integrated family of companies</p></li>
      <li class="agenda-item"><span class="agenda-num">7.</span><p class="agenda-text"><strong>Appendix:</strong>Next step…TLR Fund (2013)</p></li>
    </ol>

    <div class="pager">
      <svg viewBox="0 0 6 10" aria-hidden="true"><polyline points="5,1 1,5 5,9" fill="none" stroke="var(--muted)" stroke-width="1.4"/></svg>
      <span>02</span>
      <svg viewBox="0 0 6 10" aria-hidden="true"><polyline points="1,1 5,5 1,9" fill="none" stroke="var(--muted)" stroke-width="1.4"/></svg>
    </div>
  </section>

  <section class="slide slide--section">
    <div class="city-photo" role="img" aria-label="Blue-toned panorama of high-rise towers along a harbour"></div>
    <div class="focus-column"></div>
    <div class="brand-ribbon">
      <svg viewBox="0 0 102 96" aria-hidden="true"><polygon points="0,0 102,0 102,96 51,80 0,96" fill="var(--ribbon)"/></svg>
      <div class="brand-name">TLR</div>
    </div>
    <div class="badge"><div class="badge-inner">Green Light</div></div>
    <h2 class="section-title">MACRO-ENVIRONMENT<br>&amp; MORTAGE MARKET</h2>
    <div class="pager">
      <svg viewBox="0 0 6 10" aria-hidden="true"><polyline points="5,1 1,5 5,9" fill="none" stroke="var(--white)" stroke-width="1.4"/></svg>
      <span>03</span>
      <svg viewBox="0 0 6 10" aria-hidden="true"><polyline points="1,1 5,5 1,9" fill="none" stroke="var(--white)" stroke-width="1.4"/></svg>
    </div>
  </section>

</main>
</body>
</html>
```